Redesign current business card for food company

i would like to redesign my business card. our company is food company, our product range from chips, juices, milk and etc (mostly dried food stuff).
I want o keep same logo but , the rest is open to new design.
you can check at our website about our company www.orvelpantry.com

Target Market(s)

most of food company

Industry/Entity Type

Business

Contact Information for Business Card

I want to keep more to blue color...

Colors
3176b5
abd036

Requirements
Must have
• our old logo
Nice to have
• we do not mind to have nice material on bus card in order to accomplish nice design. for example: using spot uv, embossed and etc.

```html
<!DOCTYPE html>
<html lang="en">
<head>
<meta charset="utf-8">
<title>Orvel Business Card</title>
<link rel="stylesheet" href="https://fonts.googleapis.com/css2?family=Montserrat:wght@400;500;600;700&display=swap">
<style>
  :root {
    --backdrop: #2a2a2c;
    --teal: #0eadc9;
    --teal-light: #1ec0d8;
    --indigo: #3a3aa0;
    --indigo-dark: #2c2c8c;
    --paper: #ffffff;
  }
  * { margin: 0; padding: 0; box-sizing: border-box; }
  html, body {
    width: 1200px; height: 900px; overflow: hidden;
    background: var(--backdrop);
    font-family: "Montserrat", sans-serif;
  }
  .stage {
    position: relative; width: 1200px; height: 900px;
  }
  .card {
    position: absolute; left: 250px; width: 700px; height: 400px;
    border-radius: 22px; overflow: hidden;
  }
  .card-front { top: 35px; background: var(--teal); }
  .card-back { top: 465px; background: var(--paper); }
  .card-shapes { position: absolute; inset: 0; width: 700px; height: 400px; }

  /* front */
  .front-wordmark {
    position: absolute; left: 0; right: 0; top: 110px;
    text-align: center;
    font-size: 150px; font-weight: 600; letter-spacing: -4px;
    color: var(--indigo); line-height: 1;
  }
  .front-web {
    position: absolute; right: 40px; bottom: 80px;
    color: var(--paper); font-size: 20px; font-weight: 500; letter-spacing: 0.5px;
  }

  /* back */
  .back-wordmark {
    position: absolute; left: 48px; top: 52px;
    font-size: 104px; font-weight: 600; letter-spacing: -3px;
    color: var(--indigo); line-height: 1;
  }
  .holder {
    position: absolute; right: 40px; top: 62px; width: 270px;
    text-align: right; border-bottom: 2px solid var(--indigo); padding-bottom: 6px;
  }
  .holder-name { font-size: 21px; font-weight: 700; color: var(--indigo-dark); }
  .holder-title { font-size: 15px; font-weight: 500; color: var(--teal); margin-top: 2px; }
  .company-address {
    position: absolute; right: 40px; top: 150px; text-align: right;
    font-size: 15px; font-weight: 500; color: var(--indigo); line-height: 1.45;
  }
  .divider {
    position: absolute; left: 48px; top: 228px; width: 500px; height: 2px;
    background: var(--indigo);
  }
  .contact-list {
    position: absolute; left: 48px; top: 240px; list-style: none;
  }
  .contact-item {
    display: flex; align-items: center; gap: 12px;
    font-size: 17px; font-weight: 500; color: var(--indigo); line-height: 25px;
  }
  .contact-icon { width: 14px; height: 14px; flex: none; }
  .web-accent { color: var(--teal); font-weight: 700; }
</style>
</head>
<body>
<main class="stage">

  <section class="card card-front" aria-label="Card front">
    <svg class="card-shapes" viewBox="0 0 700 400" aria-hidden="true">
      <polygon points="0,340 430,340 500,400 0,400" fill="var(--indigo)"/>
      <polygon points="430,340 700,372 700,400 500,400" fill="var(--paper)"/>
      <polygon points="430,340 700,372 700,365 440,340" fill="var(--paper)"/>
    </svg>
    <div class="front-wordmark">orvel</div>
    <div class="front-web">www.orvelpantry.com</div>
  </section>

  <section class="card card-back" aria-label="Card back">
    <svg class="card-shapes" viewBox="0 0 700 400" aria-hidden="true">
      <polygon points="0,382 600,340 600,400 0,400" fill="var(--teal)"/>
      <polygon points="585,215 700,215 700,400 560,400" fill="var(--indigo)"/>
    </svg>
    <div class="back-wordmark">orvel</div>
    <div class="holder">
      <div class="holder-name">Daniel Hartono</div>
      <div class="holder-title">President</div>
    </div>
    <div class="company-address">
      Orvel Enterprises Corp.<br>
      2410 W Harlow Ave. Fenwick CA 90412
    </div>
    <div class="divider"></div>
    <ul class="contact-list">
      <li class="contact-item">
        <svg class="contact-icon" viewBox="0 0 16 16" aria-hidden="true"><path d="M3 1l3 3-1.5 2a9 9 0 0 0 5.5 5.5L12 10l3 3-2 2C7 15 1 9 1 3z" fill="var(--indigo)"/></svg>
        555 214 3381
      </li>
      <li class="contact-item">
        <svg class="contact-icon" viewBox="0 0 16 16" aria-hidden="true"><rect x="3" y="1" width="10" height="5" fill="var(--indigo)"/><rect x="1" y="6" width="14" height="7" rx="1" fill="var(--indigo)"/><rect x="4" y="10" width="8" height="5" fill="var(--indigo)"/></svg>
        555 214 3390
      </li>
      <li class="contact-item">
        <svg class="contact-icon" viewBox="0 0 16 16" aria-hidden="true"><rect x="4" y="1" width="8" height="14" rx="1.5" fill="none" stroke="var(--indigo)" stroke-width="1.8"/><circle cx="8" cy="12.3" r="0.9" fill="var(--indigo)"/></svg>
        555 730 6142
      </li>
      <li class="contact-item">
        <svg class="contact-icon" viewBox="0 0 16 16" aria-hidden="true"><rect x="1" y="3" width="14" height="10" rx="1" fill="none" stroke="var(--indigo)" stroke-width="1.6"/><path d="M1.5 3.5L8 9l6.5-5.5" fill="none" stroke="var(--indigo)" stroke-width="1.6"/></svg>
        daniel@orvelpantry.com
      </li>
      <li class="contact-item">
        <svg class="contact-icon" viewBox="0 0 16 16" aria-hidden="true"><circle cx="8" cy="8" r="6.5" fill="none" stroke="var(--indigo)" stroke-width="1.5"/><ellipse cx="8" cy="8" rx="2.8" ry="6.5" fill="none" stroke="var(--indigo)" stroke-width="1.2"/><path d="M1.5 8h13" stroke="var(--indigo)" stroke-width="1.2"/></svg>
        <span>www.<span class="web-accent">orvelpantry</span>.com</span>
      </li>
    </ul>
  </section>

</main>
</body>
</html>
```